Companybrochure for Consulting & Financing Firm

I need to have a Company Brochure asap for our company. We have a website that describes what we do, but we need also a brochure, that can be sent by PDF of eventually be printed as well.

The brochure should be short but nice and appealing to the customers.

We provide professional management consulting and help our customers to get finance for very diferent projects. Our business has a lot to do with personal relations, but also we are very professional in the way we work and how develop the solutions for our clients. Our clients are mainly government-owned firm, but also private trading companies and wealthy private investors.

Our customers are mainly in Latin America, but the company is headquater is in Switzerland. We are opening offices in Panama and Caracas, this should be easaly be adabtable later.

Please have a look at our website www.vorelpartners.ch. In the brochure, we would segment our services in 1.) Project Developments 2.) Management Conulting 3.) Investment Management and 4.) Finance Solutions.

Also do have a look at www.vorelpartners.ch
(Click E for the English version)
Updates

I managed to put the Mock-Up to the Website.
It is actually not really a mock-up, it is a version I have designed myself.
Well as I am not a designer, I hope you can make it much better.
The content however is what I would put in any other design as well.

Target Market(s)

Top Management, Investors, Entrepreneurs, Government Officials

Industry/Entity Type

Management Consulting

Requirements
Must have
• Design should reflect this image elements:

We are entrepreneurs.
We are comitted to get things done.
We work closely with the client side by side.
We are a professional partner.
We are not afraid of delivering unconventional solutions.
We look at the problem from various angles.
We analyse, develop solutions and implent results.
Should not have
• Typical US-American style elements. We do not want to give the impression of being a US company.

We do not want to appear to be neo-liberal. We are a politically neutral professional consulting firm.

```html
<!DOCTYPE html>
<html lang="en">
<head>
<meta charset="utf-8">
<title>Vorel Partners AG – Company Brochure</title>
<link rel="stylesheet" href="https://fonts.googleapis.com/css2?family=Exo+2:wght@600;700&family=Roboto+Condensed:wght@400;700&family=Arimo:wght@400;700&display=swap">
<style>
  :root {
    --stage: #e6e8ec;
    --paper: #ffffff;
    --sky: #d9efff;
    --grid: rgba(120, 180, 225, 0.35);
    --blue: #1a7fd0;
    --blue-deep: #0a5fb4;
    --blue-light: #1ea3ea;
    --navy: #1c1f7a;
    --ink: #222428;
    --text-navy: #1d2a5a;
    --link: #1b5fa8;
    --orange: #f4a01c;
    --red: #d8301e;
  }
  * { box-sizing: border-box; margin: 0; padding: 0; }
  html, body { width: 1200px; height: 830px; overflow: hidden; background: var(--stage); }
  .canvas { position: relative; width: 1200px; height: 830px; }

  .page {
    position: absolute; top: 26px; width: 548px; height: 776px;
    background: var(--paper); overflow: hidden;
    box-shadow: 0 2px 8px rgba(0,0,0,0.18);
  }
  .page--front { left: 32px; }
  .page--back { left: 618px; }

  .sky {
    position: absolute; left: 0; top: 0; width: 100%; height: 150px;
    background-image:
      linear-gradient(var(--grid) 1px, transparent 1px),
      linear-gradient(90deg, var(--grid) 1px, transparent 1px),
      linear-gradient(to bottom, var(--sky), #ffffff);
    background-size: 19px 19px, 19px 19px, 100% 100%;
    -webkit-mask-image: linear-gradient(to bottom, #000 40%, transparent);
            mask-image: linear-gradient(to bottom, #000 40%, transparent);
  }

  .wordmark {
    position: absolute; font-family: "Exo 2", sans-serif; font-weight: 700;
    color: var(--ink); white-space: nowrap; letter-spacing: 0.5px;
  }
  .page--front .wordmark { top: 74px; right: 28px; font-size: 33px; }
  .page--back .wordmark { top: 662px; left: 0; width: 100%; text-align: center; font-size: 22px; }

  .team-photo {
    position: absolute; left: 20px; top: 198px; width: 508px; height: 277px;
    background: radial-gradient(ellipse at 50% 55%, #4a4f5c 0%, #7d8290 40%, #e6e8ec 75%, #ffffff 100%);
  }

  .motto {
    font-family: "Exo 2", sans-serif; font-weight: 700; text-transform: uppercase;
    display: flex; align-items: center; justify-content: center; gap: 14px; white-space: nowrap;
  }
  .motto .dot {
    width: 13px; height: 13px; border-radius: 50%;
    background: radial-gradient(circle at 35% 35%, #ffe9a0, var(--orange) 60%, #c97800);
  }
  .band {
    position: absolute; left: 0; top: 475px; width: 100%; height: 59px;
    background: linear-gradient(to right, var(--blue-deep), var(--blue-light) 50%, var(--blue-deep));
  }
  .band .motto { height: 100%; color: #fff; font-size: 23px; letter-spacing: 1px; }
  .page--back .motto--header {
    position: absolute; top: 75px; left: 0; width: 100%;
    color: var(--blue-deep); font-size: 29px; letter-spacing: 1.2px; gap: 16px;
  }

  .intro {
    position: absolute; top: 561px; left: 0; width: 100%; text-align: center;
    font-family: "Arimo", sans-serif; font-weight: 700; font-size: 16px; line-height: 20px;
    color: var(--link);
  }

  .services {
    position: absolute; top: 634px; left: 32px; width: 500px; list-style: none;
    display: grid; grid-template-columns: 268px 232px; row-gap: 10px;
    font-family: "Roboto Condensed", sans-serif; font-size: 19px; color: var(--text-navy);
  }
  .services li { display: flex; align-items: center; gap: 8px; }
  .services li::before {
    content: ""; width: 14px; height: 7px; border-radius: 50%;
    background: radial-gradient(ellipse at 50% 30%, #ff9a7a, var(--red) 60%, #8a1408);
  }

  .web {
    position: absolute; top: 737px; left: 0; width: 100%; text-align: center;
    font-family: "Arimo", sans-serif; font-size: 12px; color: var(--link);
  }

  .footer-band {
    position: absolute; left: 0; bottom: 0; width: 100%; height: 19px;
    background: linear-gradient(to right, var(--navy), #2f3fb0 50%, var(--navy));
  }

  .values-panel {
    position: absolute; left: 0; top: 183px; width: 100%; height: 351px;
    background: linear-gradient(120deg, var(--blue-light), var(--blue) 55%, var(--blue-deep));
  }
  .values {
    list-style: none; padding: 33px 0 0 36px;
    font-family: "Roboto Condensed", sans-serif; font-size: 17.5px; color: #fff;
  }
  .values li { display: flex; align-items: center; gap: 9px; height: 42.4px; }
  .values svg { flex: none; }

  .registry {
    position: absolute; top: 558px; left: 0; width: 100%; text-align: center;
    font-family: "Roboto Condensed", sans-serif; font-weight: 700; font-size: 16.5px;
    color: #2b2a8a;
  }

  .contact {
    position: absolute; top: 704px; left: 26px; width: 510px;
    display: grid; grid-template-columns: 192px 176px 142px;
    font-family: "Arimo", sans-serif; font-weight: 700; font-size: 11px; line-height: 16.5px;
    color: var(--link);
  }
  .contact address { font-style: normal; }
  .contact .col-offset { padding-top: 16.5px; }
</style>
</head>
<body>
<div class="canvas">

  <section class="page page--front">
    <div class="sky"></div>
    <div class="wordmark">Vorel Partners AG</div>
    <div class="team-photo" role="img" aria-label="Photo of a smiling consultant in a dark suit standing in front of a team of business professionals"></div>
    <div class="band">
      <div class="motto"><span>Analyze</span><span class="dot"></span><span>Develop</span><span class="dot"></span><span>Deliver</span></div>
    </div>
    <p class="intro">We are a professional consulting, financing and<br>investment firm operating in the fields of:</p>
    <ul class="services">
      <li>Project Development</li>
      <li>Investment Management</li>
      <li>Management Consulting</li>
      <li>Finance Solutions</li>
    </ul>
    <div class="web">www.vorelpartners.ch</div>
    <div class="footer-band"></div>
  </section>

  <section class="page page--back">
    <div class="sky"></div>
    <div class="motto motto--header"><span>Analyze</span><span class="dot"></span><span>Develop</span><span class="dot"></span><span>Deliver</span></div>
    <div class="values-panel">
      <ul class="values">
        <li><svg width="17" height="15" viewBox="0 0 17 15"><rect x="1" y="3" width="11" height="11" fill="#fff" stroke="#f4a01c" stroke-width="2"/><path d="M3.5 8 L6.5 11 L15.5 1.5" fill="none" stroke="#f4a01c" stroke-width="2.2"/></svg>We are entrepreneurs.</li>
        <li><svg width="17" height="15" viewBox="0 0 17 15"><rect x="1" y="3" width="11" height="11" fill="#fff" stroke="#f4a01c" stroke-width="2"/><path d="M3.5 8 L6.5 11 L15.5 1.5" fill="none" stroke="#f4a01c" stroke-width="2.2"/></svg>We are comitted to get things done.</li>
        <li><svg width="17" height="15" viewBox="0 0 17 15"><rect x="1" y="3" width="11" height="11" fill="#fff" stroke="#f4a01c" stroke-width="2"/><path d="M3.5 8 L6.5 11 L15.5 1.5" fill="none" stroke="#f4a01c" stroke-width="2.2"/></svg>We work closely with the client side by side.</li>
        <li><svg width="17" height="15" viewBox="0 0 17 15"><rect x="1" y="3" width="11" height="11" fill="#fff" stroke="#f4a01c" stroke-width="2"/><path d="M3.5 8 L6.5 11 L15.5 1.5" fill="none" stroke="#f4a01c" stroke-width="2.2"/></svg>We are a professional partner.</li>
        <li><svg width="17" height="15" viewBox="0 0 17 15"><rect x="1" y="3" width="11" height="11" fill="#fff" stroke="#f4a01c" stroke-width="2"/><path d="M3.5 8 L6.5 11 L15.5 1.5" fill="none" stroke="#f4a01c" stroke-width="2.2"/></svg>We are not afraid of delivering unconventional solutions.</li>
        <li><svg width="17" height="15" viewBox="0 0 17 15"><rect x="1" y="3" width="11" height="11" fill="#fff" stroke="#f4a01c" stroke-width="2"/><path d="M3.5 8 L6.5 11 L15.5 1.5" fill="none" stroke="#f4a01c" stroke-width="2.2"/></svg>We look at the problem from various angles</li>
        <li><svg width="17" height="15" viewBox="0 0 17 15"><rect x="1" y="3" width="11" height="11" fill="#fff" stroke="#f4a01c" stroke-width="2"/><path d="M3.5 8 L6.5 11 L15.5 1.5" fill="none" stroke="#f4a01c" stroke-width="2.2"/></svg>.We analyse, develop solutions and implent results.</li>
      </ul>
    </div>
    <p class="registry">Vorel Partners AG is registered as a Swiss stock corporation since 1995.</p>
    <div class="wordmark">Vorel Partners AG</div>
    <div class="contact">
      <address>Vorel Partners AG<br>Lindenhof-Strasse 14<br>CH-8001 Zürich</address>
      <div class="col-offset">Tel.&nbsp; +41 44 512 30 10<br>Fax. +41 44 512 30 11</div>
      <div class="col-offset">www.vorelpartners.ch<br>info@vorelpartners.ch</div>
    </div>
    <div class="footer-band"></div>
  </section>

</div>
</body>
</html>
```